Harborline Auto LLC

Car Dealer Customer Service
Address: 2874 Cresthaven Road, Shelbyville, TN 37162
web: www.harborlineautoxq.net
email: harborlineautoxq@mailnest.example
Phone: (931) 555-0148
Phone: (629) 555-0173

```html
<!DOCTYPE html>
<html lang="en">
<head>
<meta charset="utf-8">
<title>Harborline Auto – Business Card</title>
<link href="https://fonts.googleapis.com/css2?family=Bebas+Neue&family=Montserrat:wght@800&family=Arimo:wght@400&display=swap" rel="stylesheet">
<style>
  :root {
    --page-bg: #a9a9a9;
    --brand-blue: #1a77aa;
    --brand-blue-light: #2591ca;
    --brand-blue-dark: #14567b;
    --brand-gold: #ecb142;
    --white: #ffffff;
    --rule: rgba(255,255,255,0.55);
  }
  * { margin: 0; padding: 0; box-sizing: border-box; }
  html, body { width: 1200px; height: 1200px; overflow: hidden; }
  body { background: var(--page-bg); position: relative; }

  .card { position: absolute; top: 303px; height: 594px; box-shadow: 3px 4px 6px rgba(0,0,0,0.35); }

  /* Front */
  .card-front {
    left: 201px; width: 369px;
    background: linear-gradient(180deg, var(--brand-blue-light) 0%, #4f9fcb 25%, #3a86b3 50%, #226e9b 75%, var(--brand-blue-dark) 100%);
  }
  .tagline { position: absolute; left: 0; right: 0; text-align: center; color: var(--white);
    font-family: "Bebas Neue", "Arial Narrow", sans-serif; line-height: 1; }
  .tagline-car { top: 156px; font-size: 80px; letter-spacing: 2px; }
  .tagline-customer { top: 540px; }
  .tagline-line2 { top: 241px; font-size: 93px; letter-spacing: 1px; }
  .tagline-line3 { top: 341px; font-size: 113px; letter-spacing: 7px; padding-left: 7px; }

  /* Back */
  .card-back { left: 599px; width: 364px; background: var(--brand-blue); overflow: hidden; }
  .brand-area { position: absolute; left: 0; top: 0; width: 100%; height: 290px; background: var(--white); }
  .brand-dot { position: absolute; left: 132px; top: 84px; width: 100px; height: 100px; border-radius: 50%; background: var(--brand-blue-light); }
  .brand-name { position: absolute; left: 0; right: 0; top: 222px; text-align: center;
    font-family: "Montserrat", sans-serif; font-weight: 800; font-size: 30px; color: var(--brand-blue); letter-spacing: 0.5px; }
  .gold-band { position: absolute; left: 0; top: 290px; width: 100%; height: 6px; background: var(--brand-gold); }

  .contact { position: absolute; left: 0; right: 0; text-align: center; color: var(--white);
    font-family: "Arimo", Arial, sans-serif; }
  .person-name { position: absolute; left: 0; right: 0; top: 327px; text-align: center; color: var(--white);
    font-family: "Montserrat", sans-serif; font-weight: 800; font-size: 20px; }
  .person-title { top: 349px; font-size: 17px; }

  .icon-row { position: absolute; left: 0; right: 0; top: 378px; display: flex; justify-content: center; align-items: center; gap: 5px; }
  .icon-row .rule { width: 32px; height: 1px; background: var(--rule); margin: 0 6px; }
  .icon-box { width: 25px; height: 25px; background: var(--white); border-radius: 3px; display: flex; align-items: center; justify-content: center; }

  .contact-lines { top: 414px; font-size: 16.5px; line-height: 21.5px; }
  .divider { position: absolute; left: 89px; width: 195px; top: 512px; height: 1px; background: var(--rule); }
  .address { top: 522px; font-size: 16.5px; line-height: 21.5px; }
</style>
</head>
<body>

<section class="card card-front" role="img" aria-label="Blue gradient card front">
  <div class="tagline tagline-car">Car Dealer</div>
  <div class="tagline tagline-line2">Customer</div>
  <div class="tagline tagline-line3">Service</div>
</section>

<section class="card card-back">
  <div class="brand-area">
    <div class="brand-dot"></div>
    <div class="brand-name">HARBORLINE AUTO</div>
  </div>
  <div class="gold-band"></div>

  <div class="person-name">DANIEL WHITMORE</div>
  <div class="contact person-title">Managing Director</div>

  <div class="icon-row">
    <span class="rule"></span>
    <span class="icon-box">
      <svg width="17" height="15" viewBox="0 0 17 15"><path d="M1 6 Q8.5 0 16 6 L14 8 L12 6.5 L12 4.5 Q8.5 3 5 4.5 L5 6.5 L3 8 Z" fill="#1a77aa"/><path d="M4 9 L6 6 L11 6 L13 9 L13 14 L4 14 Z" fill="#1a77aa"/></svg>
    </span>
    <span class="icon-box">
      <svg width="17" height="15" viewBox="0 0 17 15"><path d="M1 6 Q8.5 0 16 6 L14 8 L12 6.5 L12 4.5 Q8.5 3 5 4.5 L5 6.5 L3 8 Z" fill="#1a77aa"/><path d="M4 9 L6 6 L11 6 L13 9 L13 14 L4 14 Z" fill="#1a77aa"/></svg>
    </span>
    <span class="icon-box">
      <svg width="17" height="17" viewBox="0 0 17 17"><circle cx="8.5" cy="8.5" r="7.5" fill="#1a77aa"/><ellipse cx="8.5" cy="8.5" rx="3.2" ry="7.5" fill="none" stroke="#fff" stroke-width="1"/><line x1="1" y1="8.5" x2="16" y2="8.5" stroke="#fff" stroke-width="1"/></svg>
    </span>
    <span class="icon-box">
      <svg width="17" height="13" viewBox="0 0 17 13"><rect x="0.5" y="0.5" width="16" height="12" fill="none" stroke="#1a77aa" stroke-width="1.2"/><path d="M0.5 0.5 L8.5 7 L16.5 0.5 M0.5 12.5 L6.5 5.5 M16.5 12.5 L10.5 5.5" fill="none" stroke="#1a77aa" stroke-width="1.2"/></svg>
    </span>
    <span class="rule"></span>
  </div>

  <div class="contact contact-lines">
    (931) 555-0148<br>
    (629) 555-0173<br>
    www.harborlineautoxq.net<br>
    harborlineautoxq@mailnest.example
  </div>
  <div class="divider"></div>
  <div class="contact address">
    2874 Cresthaven Road<br>
    Shelbyville, TN 37162
  </div>
</section>

</body>
</html>
```